Steady Hands, professional newsletter for GAPM

** updated based on results so far** We need a 2 page newsletter designed on both sides of an 8.6 x 11 sheet back and front. Page one needs our logo below, name steady hands in large letters tagline of official newsletter of the guild of acute practice medicine volume and issue number locations It needs to include five locations for 250-400 word articles each with a spot for a picture. Page 2 needs to include contact information including address, phone number, email, twitter and facebook info below. The design need to complement out log in color, be professional with clean lines and easy to follow. We are a non profit organization dedicated to providers of urgent care medicine.

Target Market(s)

Physicians, Nurse Practitioners, Physician Assistants

Requirements
Must have
• 2 pages, back and front 8.5x 11
• 5 article area 250-400 words, one image for each
• our logo
• Name: Steady Hands - page one large visible print
• Contact inf:
• Guild of Acute Practice Medicine
• 912 Larkmoor Ave. Suite 418E
• Naperville, IL 60563
• 1 855-314-7093
• Info@gaopm.org
• @GuildAPM
Nice to have
• ease of entering info
• professional clean lines

```html
<!DOCTYPE html>
<html lang="en">
<head>
<meta charset="utf-8">
<title>Steady Hands – Newsletter Back Page</title>
<link href="https://fonts.googleapis.com/css2?family=Source+Sans+3:wght@400;700&family=Roboto+Slab:wght@300&family=Roboto:wght@300&display=swap" rel="stylesheet">
<style>
  :root {
    --ink: #2b2b2b;
    --body-ink: #3a3330;
    --orange: #f0962a;
    --panel: rgba(58, 58, 58, 0.93);
    --white: #ffffff;
    --card-top: rgba(246, 226, 222, 0.82);
    --card-bottom: rgba(196, 120, 78, 0.92);
    --card-edge: rgba(170, 110, 60, 0.6);
  }
  html, body { margin: 0; padding: 0; overflow: hidden; }
  body { width: 938px; height: 1200px; background: #e9e6e3; }
  .page {
    position: relative; width: 938px; height: 1200px; overflow: hidden;
    font-family: "Source Sans 3", sans-serif; color: var(--ink);
  }
  .backdrop {
    position: absolute; inset: 0;
    background:
      radial-gradient(ellipse at 50% 40%, rgba(240,232,226,0.9) 0%, rgba(240,232,226,0) 45%),
      linear-gradient(90deg, #b99a80 0%, #d9cfc6 30%, #c9b9ac 55%, #cbbdb1 75%, #b39479 100%);
  }
  .care-scene {
    position: absolute; left: 496px; top: 704px; width: 442px; height: 496px;
    background: linear-gradient(160deg, #eef0f0 0%, #e3e2e6 40%, #dcb7cc 70%, #d8d9e2 100%);
  }
  .article {
    position: absolute; left: 51px; width: 837px; height: 146px; box-sizing: border-box;
    border: 1px solid var(--card-edge); border-radius: 14px;
    background: linear-gradient(180deg, var(--card-top) 0%, rgba(226,178,150,0.88) 55%, var(--card-bottom) 100%);
  }
  .article-photo {
    position: absolute; left: 25px; top: 12px; width: 120px; height: 120px; box-sizing: border-box;
    border: 4px solid var(--orange); border-radius: 8px;
    background: linear-gradient(135deg, #e8e0cf 0%, #b6b2a8 50%, #efe8dc 100%);
  }
  .article-title {
    position: absolute; left: 164px; top: 16px; margin: 0;
    font-size: 20px; font-weight: 700; color: var(--ink); letter-spacing: 0.2px;
  }
  .article-text {
    position: absolute; left: 164px; top: 51px; width: 620px; margin: 0;
    font-size: 10.8px; line-height: 18.3px; color: var(--body-ink);
  }
  .contact-panel {
    position: absolute; left: 51px; top: 726px; width: 443px; height: 442px;
    background: var(--panel); border-radius: 8px; color: var(--white);
  }
  .accent-bar {
    position: absolute; left: 482px; top: 746px; width: 26px; height: 403px;
    background: var(--orange); border-radius: 13px;
  }
  .contact-icon { position: absolute; }
  .contact-line {
    position: absolute; left: 106px; margin: 0;
    font-family: "Roboto Slab", serif; font-weight: 300; color: var(--white);
  }
  .address { top: 40px; font-size: 20.5px; line-height: 28px; }
  .online { top: 152px; font-size: 20.5px; line-height: 33px; }
  .phone {
    position: absolute; left: 106px; top: 228px; margin: 0;
    font-family: "Roboto", sans-serif; font-weight: 300; font-size: 45px; color: var(--white);
  }
  .social { font-size: 20.5px; line-height: 26px; left: 101px; }
  .social-circle {
    position: absolute; left: 41px; width: 40px; height: 40px; box-sizing: border-box;
    border: 2.5px solid var(--white); border-radius: 50%;
  }
</style>
</head>
<body>
<div class="page">
  <div class="backdrop" role="img" aria-label="Softly blurred hospital corridor in warm beige tones"></div>
  <div class="care-scene" role="img" aria-label="Nurse kneeling beside a smiling patient in a wheelchair in a bright hospital hallway"></div>

  <article class="article" style="top:42px">
    <div class="article-photo" role="img" aria-label="Three students practising resuscitation on a training mannequin"></div>
    <h2 class="article-title">Place 01</h2>
    <p class="article-text">Lorem ipsum dolor sit amet, consectetur adipisicing elit, sed do eiusmod tempor incididunt ut labore et dolore magna aliqua. Ut enim ad minim veniam, quis nostrud exercitation ullamco laboris nisi ut aliquip ex ea commodo consequat. Duis aute irure dolor in reprehenderit in voluptate velit esse cillum dolore eu fugiat nulla pariatur. Excepteur sint occaecat cup­idatat non proident, sunt in culpa qui officia deserunt mollit anim id est laborum. Sed ut perspiciatis unde omnis iste natus</p>
  </article>
  <article class="article" style="top:214px">
    <div class="article-photo" role="img" aria-label="Three students practising resuscitation on a training mannequin"></div>
    <h2 class="article-title">Place 01</h2>
    <p class="article-text">Lorem ipsum dolor sit amet, consectetur adipisicing elit, sed do eiusmod tempor incididunt ut labore et dolore magna aliqua. Ut enim ad minim veniam, quis nostrud exercitation ullamco laboris nisi ut aliquip ex ea commodo consequat. Duis aute irure dolor in reprehenderit in voluptate velit esse cillum dolore eu fugiat nulla pariatur. Excepteur sint occaecat cup­idatat non proident, sunt in culpa qui officia deserunt mollit anim id est laborum. Sed ut perspiciatis unde omnis iste natus</p>
  </article>
  <article class="article" style="top:386px">
    <div class="article-photo" role="img" aria-label="Three students practising resuscitation on a training mannequin"></div>
    <h2 class="article-title">Place 01</h2>
    <p class="article-text">Lorem ipsum dolor sit amet, consectetur adipisicing elit, sed do eiusmod tempor incididunt ut labore et dolore magna aliqua. Ut enim ad minim veniam, quis nostrud exercitation ullamco laboris nisi ut aliquip ex ea commodo consequat. Duis aute irure dolor in reprehenderit in voluptate velit esse cillum dolore eu fugiat nulla pariatur. Excepteur sint occaecat cup­idatat non proident, sunt in culpa qui officia deserunt mollit anim id est laborum. Sed ut perspiciatis unde omnis iste natus</p>
  </article>
  <article class="article" style="top:558px">
    <div class="article-photo" role="img" aria-label="Three students practising resuscitation on a training mannequin"></div>
    <h2 class="article-title">Place 01</h2>
    <p class="article-text">Lorem ipsum dolor sit amet, consectetur adipisicing elit, sed do eiusmod tempor incididunt ut labore et dolore magna aliqua. Ut enim ad minim veniam, quis nostrud exercitation ullamco laboris nisi ut aliquip ex ea commodo consequat. Duis aute irure dolor in reprehenderit in voluptate velit esse cillum dolore eu fugiat nulla pariatur. Excepteur sint occaecat cup­idatat non proident, sunt in culpa qui officia deserunt mollit anim id est laborum. Sed ut perspiciatis unde omnis iste natus</p>
  </article>

  <section class="contact-panel">
    <svg class="contact-icon" style="left:43px;top:60px" width="38" height="34" viewBox="0 0 38 34" aria-hidden="true">
      <path d="M0 17 L38 0 L22 34 L17 21 Z" fill="#fff"/>
      <path d="M17 21 L38 0" stroke="#3a3a3a" stroke-width="2"/>
    </svg>
    <p class="contact-line address">Guild of Acute Practice Medicine<br>912 Larkmoor Ave. Suite 418E<br>Naperville, IL 60563</p>

    <svg class="contact-icon" style="left:45px;top:158px" width="35" height="22" viewBox="0 0 35 22" aria-hidden="true">
      <rect x="1" y="1" width="33" height="20" fill="none" stroke="#fff" stroke-width="2"/>
      <path d="M1 1 L17.5 13 L34 1 M1 21 L13 10 M34 21 L22 10" fill="none" stroke="#fff" stroke-width="2"/>
    </svg>
    <p class="contact-line online">Info@gaopm.org<br>@GuildAPM</p>

    <svg class="contact-icon" style="left:45px;top:240px" width="34" height="34" viewBox="0 0 24 24" aria-hidden="true">
      <path d="M6.6 10.8c1.4 2.8 3.8 5.1 6.6 6.6l2.2-2.2c.3-.3.7-.4 1-.2 1.1.4 2.3.6 3.6.6.6 0 1 .4 1 1V20c0 .6-.4 1-1 1C10.6 21 3 13.4 3 4c0-.6.4-1 1-1h3.5c.6 0 1 .4 1 1 0 1.3.2 2.5.6 3.6.1.3 0 .7-.2 1z" fill="#fff"/>
    </svg>
    <p class="phone">+13 2478 52</p>

    <span class="social-circle" style="top:291px"></span>
    <p class="contact-line social" style="top:298px">www.friendwall.com/username</p>

    <span class="social-circle" style="top:352px"></span>
    <p class="contact-line social" style="top:359px">www.chirpline.com/username</p>
  </section>
  <div class="accent-bar"></div>
</div>
</body>
</html>
```